Australian Trucking Company Requires Professional Looking Stationary

We require a professional looking stationary design that incorporates our newly designed logo.

Our business, called "Brell Haulage Contracting", provides contracting work, transport and logistics to business in Western Australia particularly with links to the mining sector.

We are a small business looking to expand and our new logo and our new stationary will help develop our brand image in our market place.

Target Market(s)

Businesses and Corporation with links to the Mining Sector

Industry/Entity Type

Small Business

Requirements
Must have
• The letterhead must have the following details:
The new logo

Text saying: "Brell Holdings Pty Ltd (ACN 582 316 907) ATF The Brell Discretionary Trust T/AS"
"ABN 71 834 209 553"
Address "P.O Box 817 Wattlegrove WA, 6958"
Phone: 08 9352 7140
Email: brellhaul@mailbox-example.com.au

The text on the letterhead should be editable as the details are likely to change in the near future. Provision should be made for a website address all though one isn't available at the moment.

The styling, layout and font text is entirely up to the designer.

```html
<!DOCTYPE html>
<html lang="en">
<head>
<meta charset="utf-8">
<title>Brell Haulage Contracting – Business Card</title>
<link rel="stylesheet" href="https://fonts.googleapis.com/css2?family=Open+Sans:wght@400;600;700&display=swap">
<style>
  :root {
    --backdrop: #8a5a3a;
    --card-light: #f4f4f4;
    --card-shade: #d9d9d9;
    --brand-red: #c4101c;
    --deep-red: #8e0a12;
    --silver: #b9b9b9;
    --ink: #2a2a2a;
    --white: #ffffff;
  }
  * { box-sizing: border-box; margin: 0; padding: 0; }
  html, body { width: 1200px; height: 426px; overflow: hidden; }
  body {
    background: var(--backdrop);
    font-family: "Open Sans", Arial, sans-serif;
    position: relative;
  }
  .card {
    position: absolute;
    border-radius: 14px;
    overflow: hidden;
    box-shadow: 0 4px 10px rgba(0,0,0,.35);
  }
  .card-front {
    left: 58px; top: 48px; width: 520px; height: 292px;
    background: linear-gradient(180deg, var(--white), var(--card-light) 60%, var(--card-shade));
  }
  .card-back {
    left: 602px; top: 48px; width: 540px; height: 297px;
    background: linear-gradient(135deg, var(--white), var(--card-light) 55%, var(--card-shade));
  }
  .wave { position: absolute; inset: 0; }
  .truck-art {
    position: absolute;
    border-radius: 6px;
  }
  .truck-art--logo {
    left: 30px; top: 22px; width: 110px; height: 82px;
    background: linear-gradient(180deg, #6d6d6d, #3a3a3a);
  }
  .truck-art--band {
    left: 418px; top: 126px; width: 76px; height: 56px;
    background: linear-gradient(180deg, #5a0a0e, #2c0507);
  }
  .truck-art--hero {
    left: 160px; top: 42px; width: 320px; height: 220px;
    background: linear-gradient(180deg, #2a2a2a, #111);
    border-radius: 10px;
  }
  .brand-name {
    position: absolute; left: 158px; top: 22px;
    color: var(--brand-red);
    font-weight: 700; font-size: 27px; line-height: 30px;
  }
  .contact {
    position: absolute; left: 44px; top: 150px;
    color: var(--ink); font-size: 12px; line-height: 22px;
  }
  .contact-row { display: flex; align-items: center; gap: 14px; }
  .contact-item { display: inline-flex; align-items: center; gap: 4px; white-space: nowrap; }
  .contact-item svg { width: 11px; height: 11px; fill: var(--ink); }
  .person {
    position: absolute; left: 340px; top: 196px; width: 170px;
    text-align: center; color: var(--white);
  }
  .person-name { font-weight: 700; font-size: 18px; line-height: 22px; }
  .person-role { font-size: 12px; line-height: 16px; }
  .legal {
    position: absolute; left: 41px; top: 252px;
    color: var(--white); font-size: 11px; line-height: 17px;
  }
  .legal-abn { margin-left: 14px; }
</style>
</head>
<body>
  <section class="card card-front">
    <svg class="wave" viewBox="0 0 520 292" preserveAspectRatio="none" aria-hidden="true">
      <defs>
        <linearGradient id="redBand" x1="0" y1="0" x2="0" y2="1">
          <stop offset="0" stop-color="#e01a26"/>
          <stop offset="1" stop-color="#8e0a12"/>
        </linearGradient>
        <linearGradient id="silverBand" x1="0" y1="0" x2="1" y2="0">
          <stop offset="0" stop-color="#9d9d9d"/>
          <stop offset=".5" stop-color="#e6e6e6"/>
          <stop offset="1" stop-color="#a8a8a8"/>
        </linearGradient>
      </defs>
      <path d="M0,168 C60,200 150,204 260,160 S460,72 520,56 L520,72 C460,88 380,120 262,174 S60,214 0,186 Z" fill="url(#silverBand)"/>
      <path d="M0,180 C60,212 150,216 262,176 S460,88 520,72 L520,292 L0,292 Z" fill="url(#redBand)"/>
    </svg>

    <div class="truck-art truck-art--logo" role="img" aria-label="Grey truck illustration beside the company name"></div>
    <div class="brand-name">Brell<br>Haulage<br>Contracting</div>

    <div class="contact">
      <div class="contact-row">
        <span class="contact-item">
          <svg viewBox="0 0 24 24"><path d="M6.6 10.8a15 15 0 0 0 6.6 6.6l2.2-2.2a1 1 0 0 1 1-.25 11.4 11.4 0 0 0 3.6.57 1 1 0 0 1 1 1V20a1 1 0 0 1-1 1A17 17 0 0 1 3 4a1 1 0 0 1 1-1h3.5a1 1 0 0 1 1 1c0 1.25.2 2.45.57 3.57a1 1 0 0 1-.25 1z"/></svg>
          08 9352 7140
        </span>
        <span class="contact-item">
          <svg viewBox="0 0 24 24"><path d="M2 5h20v14H2z M4 7v.5l8 5 8-5V7z" fill-rule="evenodd"/></svg>
          brellhaul@mailbox-example.com.au
        </span>
      </div>
      <div class="contact-row">
        <span class="contact-item">
          <svg viewBox="0 0 24 24"><path d="M12 3 2 12h3v8h5v-5h4v5h5v-8h3z"/></svg>
          P.O Box 817 Wattlegrove WA, 6958
        </span>
      </div>
    </div>

    <div class="truck-art truck-art--band" role="img" aria-label="Small dark truck illustration on the red band"></div>

    <div class="person">
      <div class="person-name">Persons name</div>
      <div class="person-role">Manager</div>
    </div>

    <div class="legal">
      <div>Brell Holdings Pty Ltd (ACN 582 316 907)</div>
      <div>ATF The Brell Discretionary Trust T/AS <span class="legal-abn">ABN 71 834 209 553</span></div>
    </div>
  </section>

  <section class="card card-back">
    <div class="truck-art truck-art--hero" role="img" aria-label="Large black silhouette illustration of a truck"></div>
  </section>
</body>
</html>
```